Local Flower Farm Needs Business Card Design

I need business cards designed for a flower farm based in Eudora, Kansas.
Business Info:
We are a local cut flower farm located in Eudora, Kansas, founded by Corinne Haldwick. What started as a passion for agriculture and search for more joy in daily life has blossomed into a small business dedicated to providing the community with beautiful, fresh, and sustainable flowers. We specialize in local, seasonal blooms, ensuring that every petal reflects the care and dedication we pour into our craft. Our mission is to deliver the highest quality flowers directly to our customers through local farmers markets and to florists who share our commitment to sustainability. Join us in celebrating the beauty of nature, one bloom at a time!
Contact Details:
Corinne Haldwick
Owner
Phone 913-555-0147
Facebook: Rosalind Thorpe Gardens
Instagram: @RosalindThorpeGardens
Website: RosalindThorpeGardens.example
Target Market(s)
Wholesale to Florists and Direct to Consumer via Farmers Market
Industry/Entity Type
Florist, Farm
Contact Information for Business Card
Name, Contact Info, Logo
Look and feel
Each slider illustrates characteristics of the customer's brand and the style your logo design should communicate.

```html
<!DOCTYPE html>
<html lang="en">
<head>
<meta charset="utf-8">
<title>Rosalind Thorpe Gardens – Business Card</title>
<link rel="stylesheet" href="https://fonts.googleapis.com/css2?family=Montserrat:wght@400;500&family=Source+Sans+3:wght@700&display=swap">
<style>
  :root {
    --forest: #0b272c;
    --paper: #ffffff;
    --backdrop: #e9eaea;
    --ink: #141a1c;
    --mist: #e4e4e4;
    --muted: #3c4a4d;
  }
  * { box-sizing: border-box; margin: 0; padding: 0; }
  html, body { width: 1200px; height: 1108px; overflow: hidden; }
  body {
    background: var(--backdrop);
    position: relative;
    font-family: "Montserrat", sans-serif;
    color: var(--ink);
  }
  .card { position: absolute; left: 218px; width: 776px; }
  .card-front { top: 51px; height: 471px; background: var(--paper); }
  .card-back { top: 569px; height: 455px; background: var(--forest); }

  .name-band {
    position: absolute; left: 0; right: 0; top: 39px; height: 84px;
    background: var(--forest);
  }
  .brand-seal {
    position: absolute; left: 82px; top: 16px; width: 125px; height: 125px;
    border-radius: 50%; background: var(--paper);
    border: 3px solid var(--paper);
    box-shadow: inset 0 0 0 4px var(--paper), inset 0 0 0 5px var(--forest);
    display: flex; align-items: center; justify-content: center; text-align: center;
    font-family: "Montserrat", sans-serif; font-weight: 500;
    font-size: 13px; line-height: 1.35; letter-spacing: 1px; text-transform: uppercase;
    color: var(--forest);
  }
  .holder { position: absolute; right: 51px; top: 53px; text-align: right; color: var(--paper); }
  .holder-name { font-family: "Source Sans 3", sans-serif; font-weight: 700; font-size: 29px; line-height: 1; }
  .holder-role { font-family: "Montserrat", sans-serif; font-size: 16px; margin-top: 5px; }

  .brand-watermark {
    position: absolute; left: 513px; top: 210px; width: 215px; height: 190px;
    display: flex; align-items: center; justify-content: center; text-align: center;
    font-family: "Montserrat", sans-serif; font-weight: 500;
    font-size: 34px; line-height: 1.1; color: var(--mist);
  }

  .contact-list { position: absolute; left: 44px; top: 333px; list-style: none; }
  .contact-list li {
    display: flex; align-items: center; gap: 8px;
    font-size: 17.5px; height: 28.5px; color: var(--ink);
  }
  .contact-list svg { width: 16px; height: 16px; flex: none; }
  .dot { width: 14px; height: 14px; border-radius: 50%; background: var(--ink); flex: none; margin: 0 1px; }

  .address {
    position: absolute; left: 537px; top: 399px;
    font-size: 17.5px; line-height: 22px; color: var(--ink);
  }

  .back-ring {
    position: absolute; left: 234px; top: 89px; width: 320px; height: 320px;
    border-radius: 50%; border: 1.5px solid var(--paper);
    display: flex; align-items: center; justify-content: center; text-align: center;
    font-family: "Montserrat", sans-serif; font-weight: 500;
    font-size: 34px; line-height: 1.2; letter-spacing: 3px; text-transform: uppercase;
    color: var(--paper);
  }
</style>
</head>
<body>
  <section class="card card-front">
    <div class="name-band"></div>
    <div class="brand-seal">Rosalind<br>Thorpe<br>Gardens</div>
    <div class="holder">
      <p class="holder-name">Corinne Haldwick</p>
      <p class="holder-role">Owner</p>
    </div>

    <div class="brand-watermark" aria-hidden="true">Rosalind<br>Thorpe<br>Gardens</div>

    <ul class="contact-list">
      <li>
        <svg viewBox="0 0 24 24" aria-hidden="true"><path fill="#141a1c" d="M6.6 10.8a15.2 15.2 0 0 0 6.6 6.6l2.2-2.2a1 1 0 0 1 1-.25 11.4 11.4 0 0 0 3.6.57 1 1 0 0 1 1 1V20a1 1 0 0 1-1 1A17 17 0 0 1 3 4a1 1 0 0 1 1-1h3.5a1 1 0 0 1 1 1c0 1.25.2 2.45.57 3.57a1 1 0 0 1-.25 1z"/></svg>
        913-555-0147
      </li>
      <li><span class="dot"></span>Rosalind Thorpe Gardens</li>
      <li><span class="dot"></span>@RosalindThorpeGardens</li>
      <li>
        <svg viewBox="0 0 24 24" aria-hidden="true"><circle cx="12" cy="12" r="10" fill="#141a1c"/><path fill="none" stroke="#fff" stroke-width="1.4" d="M2 12h20M12 2c3 3 3 17 0 20M12 2c-3 3-3 17 0 20"/></svg>
        www.RosalindThorpeGardens.example
      </li>
    </ul>

    <address class="address" style="font-style:normal">418 Meadowlark Ln, #12<br>Eudora, KS 66025</address>
  </section>

  <section class="card card-back">
    <div class="back-ring">Rosalind<br>Thorpe<br>Gardens</div>
  </section>
</body>
</html>
```